MRT Property - Business Cards

Looking for a business card & general letterhead, signage etc design for our new logo.

Colours:
000a20
0056a2
00b5ef
0088ce
68cef2

Fonts:
Poppins
Karla

Please keep look and feel of new brand - example in the zip package I sent.

```html
<!DOCTYPE html>
<html lang="en">
<head>
<meta charset="UTF-8">
<title>MRT Property – Business Cards</title>
<link href="https://fonts.googleapis.com/css2?family=Poppins:wght@400;500;600&display=swap" rel="stylesheet">
<style>
  :root {
    --page-bg: #2a2b2e;
    --card-bg: #1b1c1f;
    --brand-navy: #000a20;
    --brand-blue: #0056a2;
    --brand-mid: #0088ce;
    --brand-cyan: #00b5ef;
    --brand-sky: #68cef2;
    --text-light: #ffffff;
    --rule: #6b6d72;
  }
  * { box-sizing: border-box; margin: 0; padding: 0; }
  html, body { width: 1200px; height: 1108px; overflow: hidden; }
  body {
    background: var(--page-bg);
    font-family: "Poppins", sans-serif;
    position: relative;
  }
  .card {
    position: absolute;
    top: 194px;
    width: 420px;
    height: 720px;
    border-radius: 26px;
    background: var(--card-bg);
    box-shadow: 0 18px 40px rgba(0,0,0,0.45);
    overflow: hidden;
  }
  .card--front { left: 150px; }
  .card--back { left: 630px; }

  .brand-name {
    position: absolute;
    top: 170px;
    left: 0;
    right: 0;
    text-align: center;
    font-weight: 600;
    font-size: 52px;
    letter-spacing: 1px;
    color: var(--brand-blue);
    line-height: 1;
  }

  .person {
    position: absolute;
    top: 388px;
    left: 0; right: 0;
    text-align: center;
  }
  .person__name {
    font-weight: 500;
    font-size: 27px;
    color: var(--brand-blue);
    text-transform: uppercase;
    letter-spacing: 0.5px;
    line-height: 1.1;
  }
  .person__role {
    font-size: 16px;
    color: var(--text-light);
    text-transform: uppercase;
    letter-spacing: 0.5px;
    margin-top: 4px;
  }

  .contact-icons {
    position: absolute;
    top: 478px;
    left: 40px; right: 40px;
    display: flex;
    align-items: center;
    gap: 8px;
  }
  .contact-icons .rule { flex: 1; height: 1px; background: var(--rule); }
  .icon-box {
    width: 28px; height: 28px;
    border-radius: 4px;
    background: var(--brand-blue);
    display: flex; align-items: center; justify-content: center;
  }
  .icon-box svg { width: 18px; height: 18px; }

  .contact-lines {
    position: absolute;
    top: 522px;
    left: 0; right: 0;
    text-align: center;
    color: var(--text-light);
    font-size: 18px;
    line-height: 1.35;
  }
  .divider {
    position: absolute;
    top: 614px;
    left: 70px; right: 70px;
    height: 1px;
    background: var(--rule);
  }
  .address {
    position: absolute;
    top: 630px;
    left: 0; right: 0;
    text-align: center;
    color: var(--text-light);
    font-size: 17px;
    line-height: 1.35;
  }

  .back-pattern {
    position: absolute;
    inset: 0;
    background:
      radial-gradient(ellipse at 85% 10%, rgba(160,162,168,0.55), transparent 55%),
      linear-gradient(155deg, #4a4b50 0%, #2a2b2f 45%, #101113 100%);
  }
  .back-brand {
    position: absolute;
    top: 548px;
    left: 0; right: 0;
    padding-left: 70px;
    text-align: center;
    font-weight: 600;
    font-size: 22px;
    letter-spacing: 0.5px;
    color: var(--brand-cyan);
    line-height: 1;
  }
</style>
</head>
<body>

  <section class="card card--front" aria-label="Business card front">
    <div class="brand-name">MRT Property</div>

    <div class="person">
      <p class="person__name">Daniel Hartley</p>
      <p class="person__role">Managing Director</p>
    </div>

    <div class="contact-icons">
      <span class="rule"></span>
      <span class="icon-box" aria-label="Phone">
        <svg viewBox="0 0 24 24"><path fill="#fff" d="M6.6 10.8a15 15 0 0 0 6.6 6.6l2.2-2.2a1 1 0 0 1 1-.25 11.4 11.4 0 0 0 3.6.57 1 1 0 0 1 1 1V20a1 1 0 0 1-1 1A17 17 0 0 1 3 4a1 1 0 0 1 1-1h3.5a1 1 0 0 1 1 1c0 1.25.2 2.45.57 3.57a1 1 0 0 1-.25 1z"/></svg>
      </span>
      <span class="icon-box" aria-label="Email">
        <svg viewBox="0 0 24 24"><rect x="3" y="6" width="18" height="12" rx="1" fill="none" stroke="#fff" stroke-width="2"/><path d="M3 7l9 6 9-6" fill="none" stroke="#fff" stroke-width="2"/></svg>
      </span>
      <span class="icon-box" aria-label="Website">
        <svg viewBox="0 0 24 24"><circle cx="12" cy="12" r="8" fill="none" stroke="#fff" stroke-width="2"/><path d="M4 12h16M12 4c3 3 3 13 0 16M12 4c-3 3-3 13 0 16" fill="none" stroke="#fff" stroke-width="1.5"/></svg>
      </span>
      <span class="rule"></span>
    </div>

    <div class="contact-lines">
      <p>044-555 018 273</p>
      <p>hello@mrtproperty.net</p>
      <p>www.mrtproperty.net</p>
    </div>

    <div class="divider"></div>

    <div class="address">
      <p>17, Harbour View Lane</p>
      <p>30918, Eastport</p>
    </div>
  </section>

  <section class="card card--back" aria-label="Business card back">
    <div class="back-pattern" role="img" aria-label="Glossy tonal repeat pattern across a black background, lighter towards the top right"></div>
    <div class="back-brand">MRT Property</div>
  </section>

</body>
</html>
```